Shipping and Logistics, Project

Project description : Company Profile

A total logistics company covering domestic / international freight forwarding, warehouse management services, haulage, supply chain management, transport management & distribution, procurement & assembly services, shipping, chartering & bunker services, project logistics & tax exemption consultancy, oil & gas logistics, halal logistics services & integrated logistics management. We’re a well-established and experienced freight forwarder in Kuala Lumpur, Malaysia. We specialize in customized value-added solution that optimizes your supply chain by trimming inventory, reducing logistics cost and enhancing your customer service levels.

As a member of the Worldwide Parcel and Carriage Alliance which comprise of 170 global freight agents in 80 countries that promotes great handling in cross-trade logistics and freighting. You could rely on our efficiency in handlings of export cargo (FCL, LCL, Bulk and Conventional) between our global network offices worldwide with a total scale of 10,000 groomed specialists in various logistics division working together to ensure delivery task meets with your expectation. With our dedicated qualified and experienced professionals, we are fully committed to serving our clients.

Our generic services are listed below for your reference:

• Air Freight
• Ocean Freight FCL & LCL
• Container Haulage
• Warehousing
• Transportation and Distribution within Malaysia and Thailand
• Cross-Border Road Line-hauls between Thailand, Malaysia, Singapore and Laos
• Customs Brokerage and Forwarding
• Project Cargo Freight Forwarding for setting up of new plants / factories and ad hoc heavy-lift
• Air-Sea-Road-Rail multi-modal options
• Import / Export / Storage / Documentation / Handling of DG / Hazmat
• Vessel and Aircraft Charters

Our Mission
Based on the motto “Quick, Reliable and Polite”, we are dedicated to upholding the following three points corporate philosophy:
1. Adhering to the principle that “the customer always comes first”.
2. Contributing to the development of the local community.
3. Making it our duty to be responsible and sincere.

Our Edge
• One-Stop Logistics Solutions
• Extensive Network Throughout Malaysia
• Highly Qualified and Experienced Pool of Professionals
• Comprehensive IT Solutions
• Innovative and Customer-focused Solutions
• Flexible and Consistent in Managing Exceptions
• Total Supply Chain Visibility

Target Market
1. We sell the logistics services to all the industry in Malaysia and Worldwide. (ONE Stop Logistics Solutions)

Competitor
1. TR Valmont
2. Corvessa Transport
3. Brandt + Loewe
4. FELRO
5. QTV
6. Routemarks
7. Ilto Logistics

Rules for Picking a Company Name
1. Unique and unforgettable
2. Avoid unusual spellings
3. Easy to pronounce and remember
4. Keep it simple
5. Make some sense
6. Give a clue

Rules for Picking a Company Logo
4. Keep it simple
5. Make some sense
6. Give a clue

1. Simplicity
2. Memorability
3. Originality
4. Modern Yet Timeless
5. Balance
6. Complementary
7. Versatility

Stationery Information
1. Company Name : ZENFreight Solutions Sdn Bhd
2. Company Registration : 2837165-W
3. Address : 42-08, Jalan Cempaka Indah 5, Taman Seri Bayu, 81300 Johor Bahru, Johor, Malaysia.
4. Name : Derek Tan
5. Position : Manager
6. Mobile No : (+6019) 4381907
7. Office No : (+607) 5218764
8. Fax No : Not Available
9. Email Address : derek.tan@zenfreight-solutions.example
10. Web Domain : www.zenfreight-solutions.example
11. Company Slogan : Be Globally Connected

Target Market(s)

Corporate Company

Industry/Entity Type

Shipping and Logistics Industry

Requirements
Must have
• Company Full Name : ZENFREIGHT SOLUTIONS SDN. BHD.
Nice to have
• Keep it simple and unforgettable ...

```html
<!DOCTYPE html>
<html lang="en">
<head>
<meta charset="utf-8">
<title>ZENFreight Solutions – Stationery Set</title>
<link rel="stylesheet" href="https://fonts.googleapis.com/css2?family=Poppins:wght@400;500&display=swap">
<style>
  :root {
    --backdrop: #ababab;
    --brand-blue: #3b88c9;
    --paper: #ffffff;
    --folder-grey: #e4e4e4;
    --faint-shape: #ececec;
    --folder-shape: #ebebeb;
    --ink: #222222;
    --rule: #cfcfcf;
  }
  * { margin: 0; padding: 0; box-sizing: border-box; }
  html, body { width: 1200px; height: 900px; overflow: hidden; }
  body {
    position: relative;
    background: var(--backdrop);
    font-family: "Poppins", sans-serif;
    color: var(--ink);
  }
  .piece { position: absolute; overflow: hidden; }

  /* brand name lockup */
  .brand { position: absolute; display: flex; align-items: center; color: var(--brand-blue); font-weight: 500; }
  .brand-square { background: var(--brand-blue); flex: none; }
  .brand-text { display: flex; flex-direction: column; line-height: 1; }
  .brand-name { letter-spacing: 0.02em; }
  .brand-sub { letter-spacing: 0.22em; margin-top: 0.35em; }

  .faint-disc { position: absolute; border-radius: 50%; background: var(--faint-shape); }

  /* folder */
  .folder { left: 111px; top: 144px; width: 314px; height: 436px; background: var(--folder-grey); }
  .folder .faint-disc { left: -120px; top: 103px; width: 270px; height: 270px; background: var(--folder-shape); }
  .folder .brand { right: 27px; top: 24px; gap: 8px; }
  .folder .brand-square { width: 26px; height: 26px; }
  .folder .brand-name { font-size: 15px; }
  .folder .brand-sub { font-size: 6.4px; }
  .folder-strip {
    position: absolute; left: 0; top: 368px; width: 9px; height: 68px;
    background: var(--brand-blue);
    clip-path: polygon(0 0, 100% 14%, 100% 100%, 0 100%);
  }
  .folder-slogan {
    position: absolute; left: 0; width: 312px; top: 390px; text-align: center;
    font-size: 14.5px; color: var(--brand-blue); font-weight: 400; letter-spacing: 0.01em;
  }

  /* letterhead */
  .letterhead { left: 460px; top: 154px; width: 291px; height: 425px; background: var(--paper); }
  .letterhead .faint-disc { left: 43px; top: 122px; width: 190px; height: 190px; }
  .letterhead .brand { left: 24px; top: 13px; gap: 6px; }
  .letterhead .brand-square { width: 24px; height: 24px; }
  .letterhead .brand-name { font-size: 11px; }
  .letterhead .brand-sub { font-size: 4.6px; }
  .letter-contacts {
    position: absolute; right: 19px; top: 13px; text-align: right;
    font-size: 5.4px; line-height: 6px; color: var(--ink);
  }
  .letter-contacts .accent { color: var(--brand-blue); }
  .letter-contacts .address { margin-top: 5px; }
  .letter-rule { position: absolute; left: 19px; top: 52px; width: 185px; height: 1px; background: var(--rule); }

  .footer-band {
    position: absolute; left: 0; right: 0; bottom: 0; height: 15px;
    background: var(--brand-blue); color: #fff; font-size: 5.6px;
    display: flex; align-items: center;
  }
  .letterhead .footer-band { justify-content: space-between; padding: 0 19px 0 24px; }

  /* large envelope */
  .envelope-large { left: 786px; top: 91px; width: 307px; height: 487px; }
  .envelope-large .envelope-shape { position: absolute; inset: 0; }
  .envelope-large .faint-disc { left: -66px; top: 152px; width: 284px; height: 284px; }
  .envelope-large .brand { left: 24px; top: 97px; gap: 6px; }
  .envelope-large .brand-square { width: 26px; height: 26px; }
  .envelope-large .brand-name { font-size: 11px; }
  .envelope-large .brand-sub { font-size: 4.6px; }
  .envelope-large .footer-band { justify-content: center; font-size: 5.4px; }

  /* small envelope */
  .envelope-small { left: 436px; top: 623px; width: 340px; height: 197px; }
  .envelope-small .envelope-shape { position: absolute; inset: 0; }
  .envelope-small .faint-disc { left: 200px; top: 66px; width: 116px; height: 116px; }
  .envelope-small .brand { left: 17px; top: 63px; gap: 5px; }
  .envelope-small .brand-square { width: 23px; height: 23px; }
  .envelope-small .brand-name { font-size: 10px; }
  .envelope-small .brand-sub { font-size: 4.2px; }
  .return-address { position: absolute; left: 19px; top: 165px; font-size: 5.4px; line-height: 6.4px; }
</style>
</head>
<body>

  <section class="piece folder" aria-label="Presentation folder">
    <div class="faint-disc" aria-hidden="true"></div>
    <div class="brand">
      <span class="brand-square"></span>
      <span class="brand-text"><span class="brand-name">ZENFREIGHT</span><span class="brand-sub">SOLUTIONS SDN. BHD.</span></span>
    </div>
    <div class="folder-strip"></div>
    <p class="folder-slogan">BE GLOBALLY CONNECTED</p>
  </section>

  <section class="piece letterhead" aria-label="Letterhead">
    <div class="faint-disc" aria-hidden="true"></div>
    <div class="brand">
      <span class="brand-square"></span>
      <span class="brand-text"><span class="brand-name">ZENFREIGHT</span><span class="brand-sub">SOLUTIONS SDN. BHD.</span></span>
    </div>
    <div class="letter-contacts">
      <p>(+6019) 438 1907, (+607) 521 8764</p>
      <p>derek.tan@zenfreight-solutions.example</p>
      <p>www.<span class="accent">zenfreight-solutions</span>.example</p>
      <p class="address">42-08, Jalan Cempaka Indah 5<br>Taman Seri Bayu, 81300 Johor<br>Bahru, Johor, Malaysia.</p>
    </div>
    <div class="letter-rule"></div>
    <footer class="footer-band"><span>BE GLOBALLY CONNECTED</span><span>Company No. 2837165-W</span></footer>
  </section>

  <section class="piece envelope-large" aria-label="Large envelope">
    <svg class="envelope-shape" width="307" height="487" viewBox="0 0 307 487" aria-hidden="true">
      <polygon points="0,55 307,60 307,487 0,487" fill="#ffffff"/>
      <polygon points="32,0 269,0 307,52 307,60 0,55 0,50" fill="#3b88c9"/>
    </svg>
    <div class="faint-disc" aria-hidden="true"></div>
    <div class="brand">
      <span class="brand-square"></span>
      <span class="brand-text"><span class="brand-name">ZENFREIGHT</span><span class="brand-sub">SOLUTIONS SDN. BHD.</span></span>
    </div>
    <footer class="footer-band">42-08, Jalan Cempaka Indah 5, Taman Seri Bayu, 81300 Johor Bahru, Johor, Malaysia.</footer>
  </section>

  <section class="piece envelope-small" aria-label="Small envelope">
    <svg class="envelope-shape" width="340" height="197" viewBox="0 0 340 197" aria-hidden="true">
      <rect x="0" y="26" width="340" height="171" fill="#ffffff"/>
      <polygon points="15,0 322,0 340,26 0,26" fill="#3b88c9"/>
    </svg>
    <div class="faint-disc" aria-hidden="true"></div>
    <div class="brand">
      <span class="brand-square"></span>
      <span class="brand-text"><span class="brand-name">ZENFREIGHT</span><span class="brand-sub">SOLUTIONS SDN. BHD.</span></span>
    </div>
    <p class="return-address">42-08, Jalan Cempaka Indah 5,<br>Taman Seri Bayu, 81300 Johor<br>Bahru, Johor, Malaysia.</p>
  </section>

</body>
</html>
```